K & R Acre Works. Business card design

We need a business card designed for a new business. We have a bulldozer and tractor service. We clear land and make wildlife food plots. We provide disking, bush hogging, and site prep services.
I have attached an image of a business card that I like and would like my business cards to look similar.

Target Market(s)

anyone needing bulldozer and/or tractor services

Industry/Entity Type

Business

Contact Information for Business Card

K & R Acre Works, Operated by 7-T-Ranch
Wade Colton
601-472-3358
wcr4817@fieldmail-example.com

Font styles to use
Sans Serif

Colors

Designer to choose colors to be used in the design.

Requirements
Must have
• image of tractor and bulldozer
• Land Clearing
• Wildlife food plots
• Bush Hogging
• Disking
• Site prep
Nice to have
• i have included a image of a business card that i like. I would like mine to be similar.

```html
<!DOCTYPE html>
<html lang="en">
<head>
<meta charset="utf-8">
<title>K &amp; R Acre Works – Business Card</title>
<link rel="stylesheet" href="https://fonts.googleapis.com/css2?family=Roboto:wght@400;500;700&display=swap">
<style>
  :root {
    --page-bg: #d8d8d4;
    --card-bg: #f2f2f0;
    --band-bg: #ededea;
    --olive: #8e8a2b;
    --brown: #6b3c12;
    --ink: #3a3a3a;
    --ink-dark: #222222;
    --dozer-top: #3f5a2c;
    --dozer-mid: #8a8a4a;
    --dozer-soil: #8c7a5c;
    --tractor-top: #3d6a2a;
    --tractor-mid: #6f8a3c;
    --tractor-accent: #c9542a;
  }
  html, body {
    margin: 0;
    width: 1200px;
    height: 771px;
    overflow: hidden;
    background: var(--page-bg);
  }
  .card {
    position: absolute;
    left: 75px;
    top: 85px;
    width: 1050px;
    height: 600px;
    display: block;
    font-family: "Roboto", Arial, sans-serif;
  }
  .card-face { fill: var(--card-bg); }
  .name-band { fill: var(--band-bg); }
  .brand-name { font-weight: 700; font-size: 15.5px; fill: var(--brown); letter-spacing: 0.2px; }
  .brand-tagline { font-weight: 700; font-size: 7.6px; fill: var(--ink-dark); }
  .contact-line { font-weight: 400; font-size: 8.6px; fill: var(--ink); }
  .contact-icon { fill: var(--ink); }
  .services-heading { font-weight: 500; font-size: 9.8px; fill: var(--olive); }
  .service-item { font-weight: 400; font-size: 8.6px; fill: var(--ink); }
  .service-bullet { fill: var(--olive); }
  .owner-name { font-weight: 500; font-size: 12.5px; fill: var(--olive); }
  .owner-title { font-weight: 500; font-size: 8.6px; fill: var(--brown); }
</style>
</head>
<body>
<svg class="card" viewBox="0 0 600 343" xmlns="http://www.w3.org/2000/svg">
  <defs>
    <clipPath id="card-shape">
      <rect width="600" height="343" rx="14" ry="14"/>
    </clipPath>
    <clipPath id="photo-zone">
      <path d="M600 0 L400 0 A192.6 192.6 0 0 0 400 343 L600 343 Z"/>
    </clipPath>
    <linearGradient id="dozer-tones" x1="0" y1="0" x2="0" y2="1">
      <stop offset="0" stop-color="var(--dozer-top)"/>
      <stop offset="0.5" stop-color="var(--dozer-mid)"/>
      <stop offset="1" stop-color="var(--dozer-soil)"/>
    </linearGradient>
    <linearGradient id="tractor-tones" x1="0" y1="0" x2="1" y2="1">
      <stop offset="0" stop-color="var(--tractor-top)"/>
      <stop offset="0.6" stop-color="var(--tractor-mid)"/>
      <stop offset="1" stop-color="var(--tractor-accent)"/>
    </linearGradient>
  </defs>

  <g clip-path="url(#card-shape)">
    <rect class="card-face" width="600" height="343"/>

    <g clip-path="url(#photo-zone)">
      <rect x="290" y="0" width="310" height="139" fill="url(#dozer-tones)" role="img" aria-label="Photo of a yellow bulldozer pushing soil on a cleared site"/>
      <rect class="name-band" x="290" y="139" width="310" height="65"/>
      <rect x="290" y="204" width="310" height="139" fill="url(#tractor-tones)" role="img" aria-label="Photo of an orange tractor with front loader in a grassy field"/>
    </g>

    <text class="owner-name" x="452" y="168" text-anchor="middle">WADE COLTON</text>
    <text class="owner-title" x="452" y="186" text-anchor="middle">OWNER</text>
  </g>

  <g class="brand">
    <text class="brand-name" x="48" y="70">K &amp; R ACRE WORKS</text>
    <text class="brand-tagline" x="48" y="82">FOR ALL OF YOUR LAND IMPROVEMENT NEEDS</text>
  </g>

  <g class="contacts">
    <path class="contact-icon" d="M51 150.5c0.6-0.6 1.4-0.6 1.8 0l1.2 1.6c0.3 0.5 0.2 1-0.2 1.4l-0.6 0.6c0.6 1.3 1.6 2.3 2.9 2.9l0.6-0.6c0.4-0.4 0.9-0.5 1.4-0.2l1.6 1.2c0.6 0.4 0.6 1.2 0 1.8l-0.8 0.8c-3.8 0.4-8.6-4.4-8.2-8.2z"/>
    <text class="contact-line" x="69" y="158">601-472-3358</text>

    <rect class="contact-icon" x="50" y="167.5" width="10" height="7" rx="0.6"/>
    <path d="M50.5 168 L55 171.5 L59.5 168" fill="none" stroke="var(--card-bg)" stroke-width="0.9"/>
    <text class="contact-line" x="69" y="175">wcr4817@fieldmail-example.com</text>

    <circle class="contact-icon" cx="55" cy="189" r="5"/>
    <path d="M50.5 189 H59.5 M55 184.3 C52.8 186.5 52.8 191.5 55 193.7 M55 184.3 C57.2 186.5 57.2 191.5 55 193.7" fill="none" stroke="var(--card-bg)" stroke-width="0.8"/>
    <text class="contact-line" x="69" y="192">kracreworks-example.com</text>
  </g>

  <g class="services">
    <text class="services-heading" x="48" y="225">WE CREADED</text>
    <circle class="service-bullet" cx="51" cy="239" r="1.8"/>
    <text class="service-item" x="61" y="242">Land Clearing</text>
    <circle class="service-bullet" cx="51" cy="257" r="1.8"/>
    <text class="service-item" x="61" y="260">Wildlife food plots</text>
    <circle class="service-bullet" cx="51" cy="275" r="1.8"/>
    <text class="service-item" x="61" y="278">Bush Hogging</text>
    <circle class="service-bullet" cx="51" cy="293" r="1.8"/>
    <text class="service-item" x="61" y="296">Disking</text>
    <circle class="service-bullet" cx="116" cy="293" r="1.8"/>
    <text class="service-item" x="122" y="296">Site prep</text>
  </g>
</svg>
</body>
</html>
```